Combat Sports news website design

Redesigning our existing website to make it more modern, responsive and suitable for our needs. The design needs to take in to account all aspects of our current website structure and services. View the existing website at https://www.ringpulse.co.nz

Particular attention should be paid to our livestream service, which is growing and needs to be much more user friendly to the current experience.

The homepage, article listings and article pages need designs.

Target Market(s)

Combat sports fans

Industry/Entity Type

Media

Coding

Coded - Design and coding required

Number of Pages Required

5+ page

Font styles to use
Sans Serif

Requirements
Must have
• All the functionality of the existing website must be taken in to account, and improved upon.
New design must incorporate our existing logo/colour scheme as this has only just been designed.

```html
<!DOCTYPE html>
<html lang="en">
<head>
<meta charset="utf-8">
<title>Ring Pulse — Combat Sports News</title>
<link rel="stylesheet" href="https://fonts.googleapis.com/css2?family=Mulish:wght@400;600;700;800&display=swap">
<style>
:root{
  --black:#000;
  --red:#6e0f17;
  --accent:#a3111c;
  --text:#222;
  --muted:#555;
  --panel:#f1f1f1;
  --rule:#d8d8d8;
  --footer:#232323;
  --white:#fff;
}
*{box-sizing:border-box;margin:0;padding:0}
html,body{width:1200px;height:2944px;overflow:hidden}
body{position:relative;font-family:"Mulish",sans-serif;color:var(--text);background:var(--white)}
.abs{position:absolute}
.site-header{left:0;top:0;width:1200px;height:114px;background:var(--black)}
.brand{left:75px;top:22px;color:var(--white);font-weight:800;font-size:32px;line-height:33px;letter-spacing:1px;display:flex;align-items:center;gap:10px}
.brand .dot{width:20px;height:20px;background:var(--accent)}
.brand span.sub{display:block}
.util-nav{right:75px;top:49px;display:flex;gap:12px;align-items:center;color:var(--white);font-size:13px;font-weight:700}
.util-nav .sep{font-weight:400}
.util-nav svg{margin-right:30px}
.main-nav{left:0;top:114px;width:1200px;height:69px;background:var(--red);display:flex;justify-content:center}
.main-nav a{color:var(--white);text-decoration:none;font-size:15px;font-weight:700;line-height:69px;padding:0 26.5px}
.hero{left:0;top:183px;width:1200px;height:651px;background:
  radial-gradient(circle at 62% 12%,rgba(255,236,190,.95) 0,rgba(230,170,90,.6) 10%,rgba(0,0,0,0) 30%),
  radial-gradient(ellipse 120px 260px at 6% 28%,rgba(220,170,30,.9),rgba(0,0,0,0) 80%),
  radial-gradient(ellipse 260px 180px at 60% 88%,rgba(200,25,30,.85),rgba(0,0,0,0) 80%),
  radial-gradient(ellipse 220px 300px at 62% 55%,rgba(140,80,45,.9),rgba(0,0,0,0) 80%),
  linear-gradient(180deg,#3a2416 0%,#1e130c 60%,#120b07 100%)}
.hero h1{position:absolute;left:0;right:0;top:222px;text-align:center;color:var(--white);font-size:40px;font-weight:800;line-height:50px;text-shadow:0 2px 8px rgba(0,0,0,.4)}
.dots{position:absolute;left:560px;top:593px;display:flex;gap:11px}
.dots i{width:12px;height:12px;border-radius:50%;background:var(--white)}
.section-title{font-size:33px;font-weight:700;color:#3b3b3b}
.photo{background:linear-gradient(135deg,#3a3a3a,#141414)}
.meta{font-size:12.5px;color:var(--accent)}
.meta b{font-weight:400;margin:0 7px}
.lead-title{font-size:19px;font-weight:700;color:#111;line-height:23px}
.excerpt{font-size:14px;line-height:26px;color:var(--muted)}
.side-item{left:614px;width:513px;height:117px}
.side-item .photo{position:absolute;left:0;top:0;width:167px;height:117px}
.side-item .body{position:absolute;left:185px;top:0;width:320px}
.side-item h3{font-size:16.5px;font-weight:700;line-height:22px;color:#111;width:270px}
.side-item p{font-size:13.5px;line-height:25px;color:var(--muted);margin-top:3px}
.side-item .meta{margin-top:6px}
.rule{left:75px;top:1451px;width:1052px;height:1px;background:var(--rule)}
.card{width:330px}
.card .photo{width:330px;height:214px}
.card h3{font-size:16.5px;font-weight:700;line-height:22px;color:#111;margin-top:30px;width:290px}
.card p{font-size:13.5px;line-height:25px;color:var(--muted);margin-top:2px;width:310px}
.card .meta{margin-top:8px}
.panel{left:794px;width:333px;background:var(--panel);padding:0 20px}
.panel h2{font-size:33px;font-weight:700;color:#3b3b3b}
.btn{display:inline-block;background:var(--accent);color:var(--white);font-size:15px;padding:6px 12px}
.headline{border-bottom:1px solid #cfcfcf;padding:16px 0 16px}
.headline h4{font-size:15.5px;font-weight:700;line-height:22px;color:#222}
.headline .meta{margin-top:3px}
.news-input{width:292px;height:40px;border:1px solid #bbb;background:var(--white);font-size:13px;padding:0 18px;line-height:38px;color:#333}
.news-btn{width:292px;height:38px;background:var(--accent);color:var(--white);font-size:15px;font-weight:700;text-align:center;line-height:38px;margin-top:6px}
.site-footer{left:0;top:2810px;width:1200px;height:134px;background:var(--footer);color:var(--white)}
.foot-links{position:absolute;left:74px;top:48px;font-size:13.5px;font-weight:700;display:flex;gap:16px}
.copy{position:absolute;left:74px;top:80px;font-size:13px}
.follow{position:absolute;left:954px;top:46px;font-size:13px;font-weight:700}
.socials{position:absolute;left:954px;top:72px;display:flex;gap:18px;align-items:center}
.p-lead{background:radial-gradient(ellipse 140px 120px at 58% 35%,#b07a5c,rgba(0,0,0,0) 80%),radial-gradient(ellipse 120px 70px at 62% 85%,#8a6a2a,rgba(0,0,0,0) 80%),linear-gradient(90deg,#1a1a1a,#0a0a0a)}
.p-dress{background:radial-gradient(ellipse 50px 60px at 45% 45%,#a57a5e,rgba(0,0,0,0) 85%),linear-gradient(90deg,#2a2f36,#5a5f66 50%,#1b1e22)}
.p-ring{background:radial-gradient(ellipse 30px 50px at 45% 45%,#c9b8a8,rgba(0,0,0,0) 85%),linear-gradient(180deg,#1c1c22 0%,#3a1a1e 40%,#b0202a 55%,#2a1a1e 70%,#1a1a1a)}
.p-celeb{background:radial-gradient(ellipse 45px 60px at 55% 55%,#d8b080,rgba(0,0,0,0) 85%),linear-gradient(90deg,#5a2a9a,#c02a3a 30%,#d8b23a 70%,#4a2a8a)}
.p-team{background:radial-gradient(ellipse 150px 60px at 50% 52%,#6a5a4a,rgba(0,0,0,0) 85%),linear-gradient(180deg,#1a1a22 0%,#3a3a44 35%,#2c3f6a 75%,#3a5aa0)}
.p-corner{background:radial-gradient(ellipse 50px 90px at 52% 48%,#3a3022,rgba(0,0,0,0) 85%),linear-gradient(180deg,#c8ccd4 0%,#9aa2b0 30%,#c0242c 55%,#d8d8dc 70%,#6a7a9a)}
.p-poster{background:radial-gradient(ellipse 60px 80px at 25% 40%,#8a5a4a,rgba(0,0,0,0) 85%),radial-gradient(ellipse 60px 80px at 78% 40%,#6a6aa0,rgba(0,0,0,0) 85%),radial-gradient(ellipse 110px 40px at 50% 80%,#e0a020,rgba(0,0,0,0) 85%),linear-gradient(90deg,#3a1a7a,#8a2a9a 50%,#3a2a8a)}
.p-bout{background:radial-gradient(ellipse 70px 90px at 30% 55%,#c89a7a,rgba(0,0,0,0) 85%),radial-gradient(ellipse 70px 90px at 70% 55%,#c08a6a,rgba(0,0,0,0) 85%),radial-gradient(ellipse 50px 30px at 75% 85%,#8a2a6a,rgba(0,0,0,0) 85%),linear-gradient(180deg,#e0dcd6,#8a7a6a 60%,#2a2220)}
.p-cage{background:radial-gradient(ellipse 70px 90px at 50% 50%,#3a3a3a,rgba(0,0,0,0) 85%),linear-gradient(180deg,#9a9a9a,#c8c8c8 50%,#6a6a6a)}
.p-press{background:radial-gradient(ellipse 70px 90px at 45% 50%,#a0765a,rgba(0,0,0,0) 85%),radial-gradient(ellipse 50px 60px at 90% 40%,#a0202a,rgba(0,0,0,0) 85%),linear-gradient(90deg,#2a2a2a,#3e3e3e 50%,#1c1c1c)}
</style>
</head>
<body>
<header class="abs site-header">
  <div class="abs brand"><span class="dot"></span><span>RING<span class="sub">PULSE</span></span></div>
  <nav class="abs util-nav">
    <svg width="14" height="14" viewBox="0 0 14 14"><circle cx="6" cy="6" r="4.5" stroke="#fff" stroke-width="2" fill="none"/><line x1="9.5" y1="9.5" x2="13" y2="13" stroke="#fff" stroke-width="2"/></svg>
    <span>ABOUT</span><span class="sep">/</span><span>ADVERTISE</span><span class="sep">/</span><span>LOGIN</span><span class="sep">/</span><span>REGISTER</span>
  </nav>
</header>
<nav class="abs main-nav">
  <a>HOME</a><a>MMA</a><a>KICKBOXING</a><a>BOXING</a><a>WRESTLING</a><a>GFC</a><a>PRIMEFC</a><a>LIVE EVENTS</a><a>CONTACT US</a>
</nav>
<section class="abs hero" role="img" aria-label="Boxer in red shorts and black gloves under ring lights">
  <h1>Marcel Duvane contests for WCA world title<br>at RFS 2 Nimes on June 5</h1>
  <div class="dots"><i></i><i></i><i></i><i></i></div>
</section>

<h2 class="abs section-title" style="left:76px;top:872px">Recent Headlines</h2>
<div class="abs photo p-lead" style="left:75px;top:943px;width:512px;height:265px" role="img" aria-label="Champion fighter holding a title belt"></div>
<h3 class="abs lead-title" style="left:75px;top:1229px">Rawiri Kahu flourishing under tutelage of Tom Harlow</h3>
<p class="abs excerpt" style="left:75px;top:1256px;width:515px">Rawiri Kahu is the ZFL professional bantamweight champion, winning the title with a victory over Jared Moss at ZFL 45 last October. Most recently, he defended his title last Saturday, April 17, at ZFL 48 in Dunedin, with an emphatic first-round stoppage victory over Ethan Vale.</p>
<div class="abs meta" style="left:75px;top:1371px">Apr 24 2021<b>I</b>By Admin</div>

<article class="abs side-item" style="top:943px">
  <div class="photo p-dress" role="img" aria-label="Fighter in the dressing room"></div>
  <div class="body"><h3>Rising star Niko Brandt eyes MMA career</h3><p>Niko Brandt is a young fighter stamping his name on the 75kg division.</p><div class="meta">Apr 24 2021<b>I</b>By Admin</div></div>
</article>
<article class="abs side-item" style="top:1106px">
  <div class="photo p-ring" role="img" aria-label="Kickboxer in a red-roped ring"></div>
  <div class="body"><h3>Rising star Niko Brandt eyes MMA career</h3><p>Niko Brandt is a young fighter stamping his name on the 75kg division.</p><div class="meta">Apr 24 2021<b>I</b>By Admin</div></div>
</article>
<article class="abs side-item" style="top:1267px">
  <div class="photo p-celeb" role="img" aria-label="Fighter celebrating on stage"></div>
  <div class="body"><h3>Rising star Niko Brandt eyes MMA career</h3><p>Niko Brandt is a young fighter stamping his name on the 75kg division.</p><div class="meta">Apr 24 2021<b>I</b>By Admin</div></div>
</article>

<div class="abs rule"></div>

<h2 class="abs section-title" style="left:76px;top:1488px">Earlier News</h2>

<article class="abs card" style="left:75px;top:1561px">
  <div class="photo p-team" role="img" aria-label="Team of fighters posing in the ring"></div>
  <h3>World-class action planned for Iron Will 9</h3><p>Niko Brandt is a young fighter stamping his name on the 75kg division.</p><div class="meta">Apr 24 2021<b>I</b>By Admin</div>
</article>
<article class="abs card" style="left:434px;top:1561px">
  <div class="photo p-corner" role="img" aria-label="Fighter and trainers in a red-roped ring"></div>
  <h3>Kostas Andreou fights his way to the top</h3><p>Niko Brandt is a young fighter stamping his name on the 75kg division.</p><div class="meta">Apr 24 2021<b>I</b>By Admin</div>
</article>
<article class="abs card" style="left:75px;top:1966px">
  <div class="photo p-poster" role="img" aria-label="Pay-per-view event poster with two fighters"></div>
  <h3>Fighters to do battle at Steel Storm 14</h3><p>Niko Brandt is a young fighter stamping his name on the 75kg division.</p><div class="meta">Apr 24 2021<b>I</b>By Admin</div>
</article>
<article class="abs card" style="left:434px;top:1966px">
  <div class="photo p-bout" role="img" aria-label="Two kickboxers exchanging punches"></div>
  <h3>Liam Pender ready for war at Summit MSW</h3><p>Niko Brandt is a young fighter stamping his name on the 75kg division.</p><div class="meta">Apr 24 2021<b>I</b>By Admin</div>
</article>
<article class="abs card" style="left:75px;top:2376px">
  <div class="photo p-cage" role="img" aria-label="Fighter kicking behind a cage fence"></div>
  <h3>Fighters to do battle at Steel Storm 14</h3><p>Niko Brandt is a young fighter stamping his name on the 75kg division.</p><div class="meta">Apr 24 2021<b>I</b>By Admin</div>
</article>
<article class="abs card" style="left:434px;top:2376px">
  <div class="photo p-press" role="img" aria-label="Fighter at a press interview"></div>
  <h3>Liam Pender ready for war at Summit MSW</h3><p>Niko Brandt is a young fighter stamping his name on the 75kg division.</p><div class="meta">Apr 24 2021<b>I</b>By Admin</div>
</article>

<aside class="abs panel" style="top:1497px;height:318px;padding-top:20px">
  <h2>About Us</h2>
  <p class="excerpt" style="font-size:13.5px;line-height:25px;margin-top:6px">Marina has worked in the media industry since she was 15-years-old. She has worked in both radio and print, and is the co-founder and editor-in-chief of Ring Pulse. As well as being the Ring Pulse Editor, she focuses on writing for muti-discipline combat sports.</p>
  <span class="btn" style="margin-top:12px">Read More</span>
</aside>

<aside class="abs panel" style="top:1838px;height:715px;padding-top:18px">
  <h2>Latest Headlines</h2>
  <div class="headline" style="padding-top:6px"><h4>KMT Fight Night tonight in Hamilton</h4><div class="meta">Apr 24 2021</div></div>
  <div class="headline"><h4>Reuben Tane with quick turnaround into Summit</h4><div class="meta">Apr 24 2021</div></div>
  <div class="headline"><h4>Plans for Cole Ridgeway to fight at<br>GFC 263</h4><div class="meta">Apr 24 2021</div></div>
  <div class="headline"><h4>Rawiri Kahu flourishing under tutelage of Tom Harlow</h4><div class="meta">Apr 24 2021</div></div>
  <div class="headline"><h4>Rising star Niko Brandt eyes MMA career</h4><div class="meta">Apr 24 2021</div></div>
  <div class="headline"><h4>Tariq Selim not underestimating Sean Harker</h4><div class="meta">Apr 24 2021</div></div>
  <span class="btn" style="margin-top:26px;padding:6px 24px">View All</span>
</aside>

<aside class="abs panel" style="top:2572px;height:171px;padding-top:14px">
  <h2 style="font-size:30px">Newsletter</h2>
  <div class="news-input" style="margin-top:10px">Enter Email Address</div>
  <div class="news-btn">Subscribe Now</div>
</aside>

<footer class="abs site-footer">
  <div class="foot-links"><span>SITE TERMS</span><span>/</span><span>PRIVACY</span><span>/</span><span>ADVERTISEMENT</span><span>/</span><span>CONTACT US</span></div>
  <div class="copy">Copyright © 2021 &nbsp;Company Name All Right Reserved</div>
  <div class="follow">FOLLOW US</div>
  <div class="socials">
    <svg width="22" height="22" viewBox="0 0 22 22" aria-label="Email"><rect x="2" y="5" width="18" height="12" fill="none" stroke="#fff" stroke-width="2"/><path d="M2 5l9 7 9-7" fill="none" stroke="#fff" stroke-width="2"/></svg>
    <svg width="22" height="22" viewBox="0 0 22 22" aria-label="Chat"><path d="M3 4h16v10H9l-4 4v-4H3z" fill="#fff"/></svg>
    <svg width="22" height="22" viewBox="0 0 22 22" aria-label="Share"><circle cx="5" cy="11" r="3" fill="#fff"/><circle cx="17" cy="5" r="3" fill="#fff"/><circle cx="17" cy="17" r="3" fill="#fff"/><path d="M5 11L17 5M5 11l12 6" stroke="#fff" stroke-width="2"/></svg>
    <svg width="22" height="22" viewBox="0 0 22 22" aria-label="Feed"><circle cx="5" cy="17" r="2.5" fill="#fff"/><path d="M3 10a9 9 0 0 1 9 9M3 4a15 15 0 0 1 15 15" fill="none" stroke="#fff" stroke-width="2.5"/></svg>
    <svg width="22" height="22" viewBox="0 0 22 22" aria-label="Video"><rect x="1" y="4" width="20" height="14" rx="3" fill="#fff"/><path d="M9 8l5 3-5 3z" fill="#232323"/></svg>
  </div>
</footer>
</body>
</html>
```